Business Card Design Project

Basic business card with minimal details. I just need company name, email & web address, telephone and my name.
I would like the back of the card to be grey with my logo & company name centred.

Target Market(s)

Architects
Builders
Property Developers

Industry/Entity Type

Business

Font styles to use
Sans Serif

Colors

Designer to choose colors to be used in the design.

Requirements
Must have
• Tallow Crest
Rupert Hazelby - Director
M: 0427 915203
E: rupert@tallowcrest.com.au
W: www.tallowcrest.com.au
Should not have
• No other images or pictures

```html
<!DOCTYPE html>
<html lang="en">
<head>
<meta charset="utf-8">
<title>Tallow Crest – Business Card</title>
<link rel="stylesheet" href="https://fonts.googleapis.com/css2?family=Fira+Sans+Condensed:wght@600&family=Lato:wght@400&family=Ubuntu:wght@400&display=swap">
<style>
  :root {
    --page: #eceeef;
    --card: #fbfbfb;
    --slate: #475866;
    --crimson: #a8182b;
  }
  html, body {
    margin: 0;
    width: 1200px;
    height: 864px;
    overflow: hidden;
    background: var(--page);
  }
  .card {
    position: absolute;
    left: 150px;
    top: 175px;
    width: 900px;
    height: 514px;
    background: var(--card);
    box-shadow: 0 10px 30px rgba(0,0,0,0.12);
    overflow: hidden;
    font-family: "Lato", sans-serif;
    color: var(--slate);
  }
  .brand-square {
    position: absolute;
    left: 78px;
    top: 92px;
    width: 84px;
    height: 84px;
    background: var(--crimson);
  }
  .brand-name {
    position: absolute;
    left: 192px;
    top: 92px;
    margin: 0;
    font-family: "Ubuntu", sans-serif;
    font-weight: 400;
    font-size: 72px;
    line-height: 84px;
    letter-spacing: 2px;
    text-transform: uppercase;
    color: var(--slate);
  }
  .rule {
    position: absolute;
    height: 2px;
    background: var(--crimson);
  }
  .rule--left { left: 0; top: 300px; width: 400px; }
  .rule--right { left: 700px; top: 224px; width: 200px; }
  .holder {
    position: absolute;
    right: 220px;
    top: 214px;
    text-align: right;
  }
  .holder-name {
    margin: 0;
    font-family: "Fira Sans Condensed", sans-serif;
    font-weight: 600;
    font-size: 40px;
    line-height: 44px;
    text-transform: uppercase;
    color: var(--slate);
  }
  .holder-role {
    margin: 0;
    font-family: "Fira Sans Condensed", sans-serif;
    font-weight: 600;
    font-size: 24px;
    line-height: 28px;
    color: var(--crimson);
  }
  .contacts {
    position: absolute;
    left: 450px;
    top: 338px;
    margin: 0;
    padding: 0;
    list-style: none;
  }
  .contact {
    display: flex;
    align-items: center;
    height: 40px;
    font-size: 23px;
    color: var(--slate);
  }
  .contact-icon {
    width: 24px;
    height: 24px;
    margin-right: 22px;
    fill: var(--crimson);
  }
  .address {
    position: absolute;
    left: 70px;
    top: 410px;
    margin: 0;
    font-style: normal;
    font-size: 21px;
    line-height: 32px;
    word-spacing: 8px;
    color: var(--slate);
  }
  .base-band {
    position: absolute;
    left: 0;
    bottom: 0;
    width: 100%;
    height: 24px;
    background: var(--slate);
  }
</style>
</head>
<body>
  <section class="card" aria-label="Tallow Crest business card">
    <span class="brand-square" aria-hidden="true"></span>
    <h1 class="brand-name">Tallow Crest</h1>

    <span class="rule rule--left" aria-hidden="true"></span>
    <span class="rule rule--right" aria-hidden="true"></span>

    <div class="holder">
      <p class="holder-name">Rupert Hazelby</p>
      <p class="holder-role">Director</p>
    </div>

    <ul class="contacts">
      <li class="contact">
        <svg class="contact-icon" viewBox="0 0 24 24" aria-hidden="true">
          <path d="M3 8c0-2 2-4 9-4s9 2 9 4v2h-5V8H8v2H3z"/>
          <path d="M6 11h12l2 9H4z"/>
        </svg>
        0427 915203
      </li>
      <li class="contact">
        <svg class="contact-icon" viewBox="0 0 24 24" aria-hidden="true">
          <path d="M2 5h20v14H2z"/>
          <path d="M3 6l9 7 9-7" fill="none" stroke="#fbfbfb" stroke-width="1.6"/>
        </svg>
        rupert@tallowcrest.com.au
      </li>
      <li class="contact">
        <svg class="contact-icon" viewBox="0 0 24 24" aria-hidden="true">
          <path d="M2 4h20v13H2zM4 6v9h16V6z"/>
          <path d="M11 17h2v3h-2zM7 20h10v2H7z"/>
        </svg>
        www.tallowcrest.com.au
      </li>
    </ul>

    <address class="address">Suite 4, 18 Marlow Row<br>Fenwick, VT 05471</address>

    <span class="base-band" aria-hidden="true"></span>
  </section>
</body>
</html>
```